Locksmith Business Cards

My father-in-law is in need of new business cards for his locksmith business and I need to impress him. Kindly help me out!

You can see the previous business card attached. It is a family run business in North Wales.

No individual names on the cards.

Key Things to Feature:
- The words "Prompt", "Local", "Reliable" (as you can see under the logo on the website)
- 24h Emergency Service
- Covering All of North Wales, the Wirral and Chester
- The color blue
- A key or a lock would be interesting (similar to the ones that come up when you google locksmith business card)

Optional (only if design includes bullet points, like the example below):
https://imgvaultcdn.net/samples/208314/55172/55172_3904821_208314_image.jpg
- Residential / Commercial / Automotive
- Alarms & Cameras
- Key Cutting & Safes

https://www.brynhafod-locksmiths.co.uk/

Industry/Entity Type

Locksmith

Contact Information for Business Card

01632 960 418
07700 900 362
brynhafodlocksmiths@mailvane.com
Brynhafod Locksmiths, The Willow Barn, 7 Tannery Rd., Llandudno LL99 4QX
www.brynhafod-locksmiths.co.uk

Requirements
Must have
• - The words "Prompt", "Local", "Reliable" (as you can see under the logo on the website)
• - 24h Emergency Service
• - Covering All of North Wales, the Wirral and Chester
Nice to have
• - A key or a lock would be interesting (similar to the ones that come up when you google locksmith business card)

```html
<!DOCTYPE html>
<html lang="en">
<head>
<meta charset="utf-8">
<title>Brynhafod Locksmiths – Business Cards</title>
<link href="https://fonts.googleapis.com/css2?family=Open+Sans:wght@400;600;700&family=Roboto+Condensed:wght@500;700&display=swap" rel="stylesheet">
<style>
  :root {
    --backdrop: #222325;
    --navy: #252a66;
    --mid-blue: #4a5ea6;
    --soft-blue: #5366b0;
    --white: #ffffff;
    --steel: #a9aeb2;
  }
  * { box-sizing: border-box; margin: 0; padding: 0; }
  html, body {
    width: 1200px; height: 1021px; overflow: hidden;
    background: var(--backdrop);
    font-family: "Open Sans", sans-serif;
    color: var(--white);
  }
  .card {
    position: absolute; left: 200px; width: 800px; height: 457px;
    background: var(--navy); overflow: hidden;
  }
  .card--front { top: 36px; }
  .card--back { top: 528px; }

  /* front */
  .front-edge {
    position: absolute; left: 0; top: 0; width: 250px; height: 100%;
    background: var(--white);
  }
  .front-info {
    position: absolute; left: 300px; right: 30px; top: 95px;
    text-align: center;
  }
  .brand-name {
    font-family: "Roboto Condensed", sans-serif; font-weight: 700;
    text-transform: uppercase; color: var(--white); line-height: 0.95;
  }
  .front-info .brand-name { font-size: 64px; }
  .established {
    display: flex; align-items: center; gap: 14px; justify-content: center;
    margin: 10px 0 14px; color: var(--mid-blue); font-size: 20px;
  }
  .established::before, .established::after {
    content: ""; width: 80px; height: 1px; background: var(--mid-blue);
  }
  .services { font-size: 18px; line-height: 1.3; }
  .website { margin-top: 28px; font-size: 21px; letter-spacing: 1.5px; }

  /* back */
  .back-brand {
    position: absolute; left: 44px; top: 40px;
    display: flex; align-items: center; gap: 18px;
  }
  .brand-dot { width: 72px; height: 72px; border-radius: 50%; background: var(--white); }
  .back-brand .brand-name { font-size: 54px; }
  .contacts {
    position: absolute; left: 64px; top: 180px; list-style: none;
  }
  .contacts li { display: flex; align-items: center; gap: 10px; }
  .contacts svg { width: 18px; height: 18px; fill: none; stroke: var(--mid-blue); stroke-width: 2; }
  .contact-phone { font-size: 24px; font-weight: 700; line-height: 1.2; }
  .contact-mail { font-size: 18px; margin-top: 4px; }
  .address { position: absolute; left: 64px; top: 290px; font-size: 18px; }
  .emergency-band {
    position: absolute; left: 0; top: 328px; width: 575px; height: 84px;
  }
  .emergency-title {
    background: var(--soft-blue); height: 42px; padding-left: 64px;
    display: flex; align-items: center;
    font-weight: 700; font-size: 22px; letter-spacing: 3px; text-transform: uppercase;
  }
  .coverage { padding: 8px 0 0 64px; font-size: 19px; }
  .tagline-panel {
    position: absolute; left: 590px; top: 120px; right: 0; bottom: 0;
    background: var(--white);
    display: flex; flex-direction: column; justify-content: center;
    padding-left: 40px; gap: 10px;
  }
  .tagline-panel span {
    font-family: "Roboto Condensed", sans-serif; font-weight: 700;
    font-size: 32px; color: var(--navy);
  }
</style>
</head>
<body>

<section class="card card--front">
  <div class="front-edge"></div>
  <div class="front-info">
    <div class="brand-name">Brynhafod<br>Locksmiths</div>
    <div class="established">Est Since 1989</div>
    <p class="services">Residential / Commercial / Automotive<br>Alarms &amp; Cameras<br>Key Cutting &amp; Safes</p>
    <p class="website">www.brynhafod-locksmiths.co.uk</p>
  </div>
</section>

<section class="card card--back">
  <div class="back-brand">
    <div class="brand-dot"></div>
    <div class="brand-name">Brynhafod<br>Locksmiths</div>
  </div>
  <ul class="contacts">
    <li class="contact-phone">
      <svg viewBox="0 0 24 24"><path d="M5 3h4l2 5-3 2a12 12 0 0 0 6 6l2-3 5 2v4a2 2 0 0 1-2 2A18 18 0 0 1 3 5a2 2 0 0 1 2-2z"/></svg>
      01632 960 418
    </li>
    <li class="contact-phone">
      <svg viewBox="0 0 24 24"><rect x="6" y="2" width="12" height="20" rx="2"/><line x1="11" y1="18" x2="13" y2="18"/></svg>
      07700 900 362
    </li>
    <li class="contact-mail">
      <svg viewBox="0 0 24 24"><rect x="2" y="5" width="20" height="14"/><polyline points="2,5 12,13 22,5"/></svg>
      brynhafodlocksmiths@mailvane.com
    </li>
  </ul>
  <p class="address">The Willow Barn, 7 Tannery Rd., Llandudno LL99 4QX</p>
  <div class="emergency-band">
    <div class="emergency-title">24H Emergency Service</div>
    <p class="coverage">Covering All of North Wales, the Wirral and Chester</p>
  </div>
  <div class="tagline-panel">
    <span>Prompt.</span>
    <span>Local.</span>
    <span>Reliable</span>
  </div>
</section>

</body>
</html>
```